Just Sold Postcard

Real Estate/ Brindle Oak Realty.I'd like a template that I can use to change out the picture of the home, verbiage on the front, and address. I'm including a picture of what I've used in the past. I like designs that use red, with some blue and white. I'd like the ability to change the verbiage on the back as well.

Industry/Entity Type

Real Estate

Font styles to use
Serif
Sans Serif

```html
<!DOCTYPE html>
<html lang="en">
<head>
<meta charset="utf-8">
<title>Just Sold Postcard – Brindle Oak Realty</title>
<link rel="stylesheet" href="https://fonts.googleapis.com/css2?family=Tenor+Sans&family=Mulish:wght@400;600;700&family=Marcellus&display=swap">
<style>
  :root {
    --backdrop: #333333;
    --paper: #f7f7f7;
    --brand-red: #d92626;
    --brand-blue: #21418f;
    --ink-blue: #2c3f8c;
    --white: #ffffff;
    --photo-sky: #dcdfe2;
    --photo-brick: #9a6a4e;
  }
  * { margin: 0; padding: 0; box-sizing: border-box; }
  html, body { width: 1200px; height: 1000px; overflow: hidden; }
  body { background: var(--backdrop); position: relative; font-family: "Mulish", sans-serif; }

  .postcard { position: absolute; width: 577px; height: 436px; background: var(--paper); overflow: hidden; }
  .postcard-back { left: 197px; top: 111px; }
  .postcard-front { left: 454px; top: 449px; }
  .postcard-art { position: absolute; inset: 0; }

  .brand-name {
    position: absolute; font-family: "Tenor Sans", sans-serif; color: var(--brand-blue);
    font-size: 17px; white-space: nowrap; display: flex; align-items: center; gap: 7px;
  }
  .brand-mark { width: 11px; height: 11px; background: var(--brand-red); display: inline-block; }

  /* Back */
  .back-brand { left: 58px; top: 56px; }
  .agent-name { position: absolute; left: 29px; top: 101px; font-family: "Tenor Sans", sans-serif; color: var(--ink-blue); font-size: 19px; letter-spacing: 0.5px; }
  .back-offer { position: absolute; left: 29px; top: 129px; color: var(--ink-blue); font-size: 12.5px; line-height: 16px; letter-spacing: 0.3px; }
  .back-offer strong { font-weight: 700; }
  .back-contact { position: absolute; left: 29px; top: 171px; color: var(--ink-blue); font-size: 12.5px; line-height: 16px; letter-spacing: 0.3px; }
  .back-message { position: absolute; left: 29px; top: 211px; width: 180px; color: var(--ink-blue); font-size: 10.5px; font-weight: 600; line-height: 15px; }
  .stamp-box { position: absolute; left: 442px; top: 22px; width: 114px; height: 110px; border: 3px solid var(--brand-blue); }
  .address-line { position: absolute; left: 301px; width: 255px; height: 2px; background: var(--brand-blue); }

  /* Front */
  .front-name { position: absolute; left: 39px; top: 58px; font-family: "Tenor Sans", sans-serif; color: var(--white); font-size: 34px; letter-spacing: 1px; }
  .front-phone { position: absolute; left: 39px; top: 96px; font-family: "Tenor Sans", sans-serif; color: var(--white); font-size: 16px; letter-spacing: 1px; }
  .front-offer { position: absolute; left: 39px; top: 126px; font-family: "Tenor Sans", sans-serif; color: var(--white); font-size: 14px; line-height: 18px; letter-spacing: 0.5px; }
  .front-brand { left: 350px; top: 60px; }
  .sold-headline { position: absolute; left: 43px; top: 244px; font-family: "Marcellus", serif; color: var(--brand-red); font-size: 29px; letter-spacing: 2px; font-weight: 700; }
  .sold-story { position: absolute; left: 32px; top: 290px; width: 225px; color: var(--ink-blue); font-size: 12px; line-height: 17px; letter-spacing: 0.2px; }
</style>
</head>
<body>

<section class="postcard postcard-back" aria-label="Postcard back">
  <svg class="postcard-art" viewBox="0 0 577 436" aria-hidden="true">
    <path d="M247 0 C277 70 276 185 243 255 C200 332 110 360 0 358 L0 336 C110 338 195 310 235 245 C268 185 268 70 245 0 Z" fill="var(--brand-red)"/>
    <path d="M252 0 C284 70 283 190 249 260 C205 338 110 366 0 364" fill="none" stroke="var(--brand-blue)" stroke-width="2.5"/>
  </svg>
  <div class="brand-name back-brand"><span class="brand-mark"></span>Brindle Oak Realty</div>
  <h2 class="agent-name">Marla Quinn</h2>
  <p class="back-offer">For a free Market Analysis<br>of your home. <strong>Contact&nbsp; me today</strong></p>
  <p class="back-contact">Call: (555)-014-2274<br>E: marla.quinn@example.com</p>
  <p class="back-message">Lorem ipsum dolor sit amet, consectetur adipiscing elit Duis sed eleifend ex. Donecsapien ante, fermentumnon velit convallis suscipit tortor.</p>
  <div class="stamp-box"></div>
  <div class="address-line" style="top:213px"></div>
  <div class="address-line" style="top:242px"></div>
  <div class="address-line" style="top:271px"></div>
</section>

<section class="postcard postcard-front" aria-label="Postcard front">
  <svg class="postcard-art" viewBox="0 0 577 436">
    <defs>
      <linearGradient id="house-tone" x1="0" y1="0" x2="0" y2="1">
        <stop offset="0" stop-color="var(--photo-sky)"/>
        <stop offset="0.45" stop-color="#6e6a66"/>
        <stop offset="0.75" stop-color="var(--photo-brick)"/>
        <stop offset="1" stop-color="#5d5a4c"/>
      </linearGradient>
    </defs>
    <path d="M0 0 L336 0 C350 120 280 230 170 232 C100 233 40 222 0 216 Z" fill="var(--brand-red)"/>
    <path d="M343 0 C352 50 346 95 328 125" fill="none" stroke="var(--brand-blue)" stroke-width="3"/>
    <path d="M320 436 C370 375 470 338 577 334 L577 436 Z" fill="var(--brand-red)"/>
    <path d="M312 436 C365 365 470 330 577 328 L577 334 C470 338 372 372 322 436 Z" fill="var(--brand-blue)"/>
    <rect x="0" y="395" width="322" height="41" fill="var(--brand-blue)"/>
    <circle cx="411" cy="224" r="115" fill="var(--brand-blue)"/>
    <circle cx="411" cy="224" r="109" fill="url(#house-tone)" role="img" aria-label="Photo of the sold brick house"/>
    <circle cx="317" cy="329" r="64" fill="var(--white)"/>
    <circle cx="317" cy="329" r="61" fill="var(--brand-blue)"/>
    <circle cx="317" cy="329" r="57" fill="url(#house-tone)" role="img" aria-label="Second view of the sold brick house"/>
  </svg>
  <h1 class="front-name">Marla Quinn</h1>
  <p class="front-phone">Contact&nbsp; 555-014-2274</p>
  <p class="front-offer">For free analysis of your home<br>contact me today!</p>
  <div class="brand-name front-brand"><span class="brand-mark"></span>Brindle Oak Realty</div>
  <h2 class="sold-headline">JUST SOLD!</h2>
  <p class="sold-story">Lorem ipsum dolor sit amet, consectetur adipiscing elit Duis sed eleifend ex. Donecsapien ante, fermentumnon velit at, convallis suscipit tortor. Proin elementum</p>
</section>

</body>
</html>
```